High Tech Real Estate Startup needs a business card

We are developing an innovative real estate marketing product based around advanced search and virtual reality.

We talk to people, we need business cards.

Target Market(s)

The target market is technology professionals and realtors.

Contact Information for Business Card

The information to be included will include

Name
Title
Phone Number
E-mail Address
www.zelquin.com

It should use simple iconography for each one of those fields.

Font styles to use
Other font styles liked:
• Co, Jubilat, Avenir

Colors

Designer to choose colors to be used in the design.

Requirements
Must have
• Clean aesthetic,
• Good use of negative space.
• It should use our company logo, shown in the attached file. It is able to use the negative of that logo (coloured font and white background) and I have attached other acceptable accent colours in a swatch file.
Should not have
• Should not be too busy
• No extraneous text (slogans, tag lines etc)

```html
<!DOCTYPE html>
<html lang="en">
<head>
<meta charset="utf-8">
<title>Zelquin Business Card</title>
<link href="https://fonts.googleapis.com/css2?family=Montserrat:wght@500;600;700&display=swap" rel="stylesheet">
<style>
  :root {
    --backdrop: #262626;
    --card-teal: #00bbbd;
    --ink-white: #ffffff;
    --ink-soft: #eaf7f7;
  }
  * { margin: 0; padding: 0; box-sizing: border-box; }
  html, body {
    width: 1200px;
    height: 960px;
    overflow: hidden;
    background: var(--backdrop);
  }
  .canvas {
    position: relative;
    width: 1200px;
    height: 960px;
    font-family: "Montserrat", sans-serif;
    color: var(--ink-white);
  }
  .card {
    position: absolute;
    left: 320px;
    width: 600px;
    height: 342px;
    background: var(--card-teal);
  }
  .card-front {
    top: 108px;
    display: flex;
    align-items: center;
    justify-content: center;
  }
  .brand-name {
    font-size: 78px;
    font-weight: 500;
    letter-spacing: 3px;
    line-height: 1;
    margin-top: -6px;
  }
  .card-back {
    top: 493px;
  }
  .contact-block {
    position: absolute;
    left: 0;
    right: 0;
    top: 140px;
    display: flex;
    flex-direction: column;
    align-items: center;
  }
  .identity {
    display: flex;
    align-items: baseline;
    gap: 8px;
    padding: 0 6px 4px;
    border-bottom: 1.5px solid var(--ink-soft);
  }
  .person-name {
    font-size: 27px;
    font-weight: 600;
    letter-spacing: 0.5px;
  }
  .person-title {
    font-size: 19px;
    font-weight: 600;
    letter-spacing: 0.8px;
    color: var(--ink-soft);
  }
  .contact-line {
    margin-top: 6px;
    font-size: 13.5px;
    font-weight: 700;
    letter-spacing: 0.3px;
    color: var(--ink-soft);
  }
</style>
</head>
<body>
  <main class="canvas">
    <section class="card card-front">
      <h1 class="brand-name">ZELQUIN</h1>
    </section>
    <section class="card card-back">
      <div class="contact-block">
        <p class="identity">
          <span class="person-name">DANA WHITLOW -</span>
          <span class="person-title">CEO/FOUNDER</span>
        </p>
        <p class="contact-line">555 014 2290 | dana@zelquin.com | www.zelquin.com</p>
      </div>
    </section>
  </main>
</body>
</html>
```